Awesome photographers card for an awesome new business

Double sided business card Black background and silver logo in middle on one side. Details on otherside. please keep it simple

Industry/Entity Type

Photographer

Contact Information for Business Card

Gerald Fenwick
0452817360
GeraldFenwickPhotography47@mailbox.test
www.GeraldFenwickPhotography.test.au
Instagram _Gerald_fenwick

Requirements
Must have
• My logo in Silver
• please use instagram logo instead of "Instagram"

```html
<!DOCTYPE html>
<html lang="en">
<head>
<meta charset="utf-8">
<title>Gerald Fenwick Photography – Business Card</title>
<link rel="stylesheet" href="https://fonts.googleapis.com/css2?family=Montserrat:wght@300;400&display=swap">
<style>
  :root {
    --backdrop: #161616;
    --card: #2b2b2b;
    --silver: #c9c9c9;
    --silver-soft: #a9a9a9;
  }
  * { margin: 0; padding: 0; box-sizing: border-box; }
  html, body {
    width: 1200px; height: 900px; overflow: hidden;
    background: var(--backdrop);
    font-family: "Montserrat", sans-serif;
    color: var(--silver);
  }
  .sheet {
    width: 1200px; height: 900px;
    display: flex; flex-direction: column; align-items: center; justify-content: center;
    gap: 36px;
  }
  .card {
    position: relative;
    width: 700px; height: 400px;
    background: var(--card);
    box-shadow: 0 10px 30px rgba(0,0,0,0.5);
  }
  /* Front */
  .card-front { display: flex; align-items: center; justify-content: center; }
  .brand { display: flex; align-items: center; gap: 14px; }
  .brand-dot {
    width: 18px; height: 18px; border-radius: 50%;
    border: 1.5px solid var(--silver);
  }
  .brand-name {
    font-weight: 300; font-size: 26px; letter-spacing: 4px;
    text-transform: uppercase; color: var(--silver);
  }
  /* Back */
  .holder-name {
    position: absolute; left: 44px; top: 40px;
    font-weight: 400; font-size: 18px; letter-spacing: 4px;
    text-transform: uppercase; color: var(--silver);
  }
  .back-brand {
    position: absolute; right: 60px; top: 140px;
    font-weight: 300; font-size: 22px; letter-spacing: 3px;
    text-transform: uppercase; color: var(--silver);
  }
  .contact-list {
    position: absolute; left: 44px; bottom: 44px;
    list-style: none; display: flex; flex-direction: column; gap: 6px;
    font-weight: 300; font-size: 15px; letter-spacing: 0.8px; color: var(--silver);
  }
  .contact-list li { display: flex; align-items: center; gap: 14px; }
  .contact-icon { width: 14px; height: 14px; flex: none; fill: var(--silver-soft); }
  .social {
    position: absolute; right: 44px; bottom: 44px;
    display: flex; align-items: center; gap: 8px;
    font-weight: 300; font-size: 15px; letter-spacing: 0.8px;
  }
  .social-mark {
    width: 14px; height: 14px; border-radius: 50%;
    border: 1.5px solid var(--silver);
  }
</style>
</head>
<body>
<main class="sheet">
  <section class="card card-front" aria-label="Card front">
    <div class="brand">
      <span class="brand-dot"></span>
      <span class="brand-name">Gerald Fenwick Photography</span>
    </div>
  </section>

  <section class="card card-back" aria-label="Card back">
    <h1 class="holder-name">Gerald Fenwick</h1>
    <div class="back-brand">Gerald Fenwick</div>

    <ul class="contact-list">
      <li>
        <svg class="contact-icon" viewBox="0 0 16 16" aria-hidden="true">
          <path d="M3.5 1.5l2.5 0 1 3.5-1.8 1.2a9 9 0 0 0 4.6 4.6L11 9l3.5 1v2.5c0 1-1 2-2 2A11 11 0 0 1 1.5 3.5c0-1 1-2 2-2z"/>
        </svg>
        <span>0452817360</span>
      </li>
      <li>
        <svg class="contact-icon" viewBox="0 0 16 16" aria-hidden="true">
          <path d="M1 3h14v10H1z M1.5 3.5L8 9l6.5-5.5" fill="none" stroke="#a9a9a9" stroke-width="1.5"/>
        </svg>
        <span>GeraldFenwickPhotography47@mailbox.test</span>
      </li>
      <li>
        <svg class="contact-icon" viewBox="0 0 16 16" aria-hidden="true">
          <g fill="none" stroke="#a9a9a9" stroke-width="1.3">
            <circle cx="8" cy="8" r="6.5"/>
            <ellipse cx="8" cy="8" rx="2.8" ry="6.5"/>
            <path d="M1.5 8h13"/>
          </g>
        </svg>
        <span>www.GeraldFenwickPhotography.test.au</span>
      </li>
    </ul>

    <div class="social">
      <span class="social-mark"></span>
      <span>_Gerald_fenwick</span>
    </div>
  </section>
</main>
</body>
</html>
```